UL Aesthetic improvement on full website

brightneighbourhq.com
We need someone to improve the current website brightneighbourhq.com
Some designed to fail to follow isntruction and deliver. please find attached summary latest design requirement, please follow and read each of the requirements carefully and submit max two versions only. The winner would have to deliver within 5 days

Sample reference : velmorq.com/html/brightneighbour/#
(previous winner cant deliver)
*All of our wording and graphic content are updated, designer wouldn't involve in recreating any content.
Designer may use template or own material. delivery in html and implement on our WordPress server

please submit about us the project submission.
upon the winning, you have to maintain sub content / pages and submit the full site with your improved version of full websites including inner pages

Low design quality

Target Market(s)

general audience

Industry/Entity Type

social service

Number of Pages Required

5+ page

Requirements
Must have
• feeling and look similar to pobrix dot com
Nice to have
• extend the same style to other pages

```html
<!DOCTYPE html>
<html lang="en">
<head>
<meta charset="utf-8">
<title>Bright Neighbour — Home and About Us</title>
<link href="https://fonts.googleapis.com/css2?family=Poppins:wght@300;400;500;600&display=swap" rel="stylesheet">
<style>
:root{
  --coral:#f87171;
  --blush:#ffd3d5;
  --peach:#fdd6bd;
  --butter:#fbe6a6;
  --ink:#161616;
  --body:#5a5a5a;
  --stage:#f3f3f3;
  --frame:#1d1d1d;
}
*{box-sizing:border-box;margin:0;padding:0}
html,body{width:731px;height:1200px;overflow:hidden;background:var(--stage)}
body{font-family:'Poppins',sans-serif;color:var(--ink)}
.stage{position:absolute;left:0;top:0;width:1500px;height:2464px;transform:scale(.4873);transform-origin:0 0}
.page{position:absolute;top:0;height:2464px;background:#fff;overflow:hidden;box-shadow:0 0 30px rgba(0,0,0,.05)}
.page--home{left:122px;width:482px}
.page--about{left:680px;width:642px}
.backdrop{position:absolute;left:0;top:0}
.a{position:absolute;white-space:nowrap}
.eyebrow{color:var(--coral);font-weight:500;letter-spacing:.06em;text-transform:uppercase}
.heading{font-weight:500;color:var(--ink);line-height:1.15}
.copy{color:var(--body);font-weight:300;line-height:1.55;white-space:normal}
.link{color:var(--coral)}
.pill{position:absolute;border-radius:999px;display:flex;align-items:center;justify-content:center;font-weight:500;text-transform:uppercase;white-space:nowrap}
.pill--coral{background:var(--coral);color:#fff}
.pill--dark{background:var(--ink);color:#fff}
.pill--white{background:#fff;color:var(--ink)}
.pill--outline{border:1px solid var(--coral);color:var(--coral);background:#fff}
.logo-dot{position:absolute;border-radius:50%;background:var(--coral);color:#fff;display:flex;align-items:center;justify-content:center;text-align:center;font-weight:500;line-height:1.05;letter-spacing:.04em}
.nav a{position:absolute;color:var(--ink);text-decoration:none;white-space:nowrap}
.nav a.is-active{color:var(--coral)}
.nav a.is-active::after{content:"";position:absolute;left:0;right:0;bottom:-6px;height:1px;background:var(--coral)}
.photo{position:absolute;border-radius:8px;overflow:hidden}
.card{position:absolute;background:#fff;border-radius:10px;box-shadow:0 6px 18px rgba(240,120,120,.12)}
.badge{position:absolute;border-radius:20px;background:#eef0f3;border:1px solid #dde0e5}
.partner{position:absolute;border-radius:4px}
.field{position:absolute;background:#fff;border-radius:999px;display:flex;align-items:center;color:var(--ink)}
.check{position:absolute;border-radius:50%;background:var(--coral)}
.faq-item{position:absolute;left:53px;width:262px;height:21px;border:1px solid #d9d9d9;border-radius:999px;font-size:6.2px;display:flex;align-items:center;padding-left:14px;color:var(--ink);white-space:nowrap;overflow:hidden}
.bullets{position:absolute;list-style:none;color:var(--ink);text-transform:uppercase;white-space:nowrap}
.bullets li{position:relative;padding-left:14px}
.bullets li::before{content:"";position:absolute;left:0;top:50%;width:5px;height:5px;border-radius:50%;background:var(--coral);transform:translateY(-50%)}
.page--about .bullets li::before{width:6px;height:6px}
.social{position:absolute;border-radius:50%;background:var(--ink)}
.copyright{position:absolute;left:0;right:0;text-align:center;color:var(--ink);text-transform:uppercase}

/* phone mockup */
.phone{position:absolute;background:var(--frame);border-radius:2em;padding:.45em;box-shadow:0 .8em 2em rgba(0,0,0,.18)}
.phone--crop{border-radius:2em 2em 0 0;padding-bottom:0}
.screen{position:relative;width:100%;height:100%;background:#fff;border-radius:1.6em;overflow:hidden;padding:1.6em .9em 0}
.phone--crop .screen{border-radius:1.6em 1.6em 0 0}
.notch{position:absolute;top:0;left:50%;transform:translateX(-50%);width:5.5em;height:1em;background:var(--frame);border-radius:0 0 .8em .8em}
.ui-head{display:flex;align-items:center;gap:.4em;margin-bottom:.6em}
.ui-head .grow{flex:1}
.ui-dot{width:1.2em;height:1.2em;border-radius:50%;background:#f8a3a3}
.ui-dot--ring{background:#fff;border:.15em solid #f8a3a3}
.ui-search{height:1.5em;border-radius:.75em;background:#f1f1f1;margin-bottom:.9em}
.ui-grid{display:grid;grid-template-columns:repeat(4,1fr);gap:.7em .9em;margin-bottom:.9em}
.ui-grid i{display:block;height:2.1em;border:.1em solid #f6b0b0;border-radius:.45em}
.ui-line{height:.45em;background:#3a3a3a;border-radius:.2em;width:55%;margin-bottom:.35em}
.ui-line--soft{background:#d4d4d4;width:75%}
.ui-line--short{width:30%}
.ui-tiles{display:flex;gap:.5em;margin-top:.4em}
.ui-tiles i{flex:1;height:4em;border-radius:.35em;background:linear-gradient(135deg,#f2d7b0,#c8834f)}
.ui-tiles i+i{background:linear-gradient(135deg,#f87171,#e0452e)}
.ui-tabs{display:flex;margin:.6em 0 .5em;border-bottom:.1em solid #eee}
.ui-tabs i{flex:1;height:1.2em}
.ui-tabs i:first-child{border-bottom:.2em solid var(--coral)}
.ui-row{display:flex;gap:.6em;align-items:center;padding:.7em 0;border-bottom:.1em solid #f0f0f0}
.ui-thumb{width:3.4em;height:2.7em;border-radius:.35em;background:radial-gradient(circle at 40% 45%,#f5e1a8,#d9a05e 55%,#8f6a3c)}
.ui-text{flex:1}
.ui-banner{height:4.2em;border-radius:.4em;background:linear-gradient(90deg,#f4a79b 0 38%,#9fd6ea 38%);margin-bottom:.8em}
.ui-nav{position:absolute;left:0;right:0;bottom:0;height:1.8em;border-top:.1em solid #eee;display:flex;justify-content:space-around;align-items:center}
.ui-nav i{width:.9em;height:.9em;border-radius:50%;background:#ddd}
.ui-nav i:first-child{background:var(--coral)}
</style>
</head>
<body>
<div class="stage">

  <section class="page page--home">
    <svg class="backdrop" width="482" height="2464" viewBox="0 0 482 2464" aria-hidden="true">
      <defs>
        <linearGradient id="homeHero" x1="0" y1="0" x2="0" y2="1">
          <stop offset="0" stop-color="#fff6f6"/>
          <stop offset="1" stop-color="#ffd3d5"/>
        </linearGradient>
        <linearGradient id="homeFoot" x1="0" y1="0" x2="0" y2="1">
          <stop offset="0" stop-color="#ffd9db"/>
          <stop offset="1" stop-color="#ffe9ea"/>
        </linearGradient>
      </defs>
      <path d="M160 0 H482 V185 C430 205 385 150 335 105 C285 60 205 55 160 0Z" fill="#ffd6d8"/>
      <path d="M0 272 C150 252 300 292 482 240 V1082 C350 1112 150 1090 0 1108Z" fill="url(#homeHero)"/>
      <path d="M0 1328 C150 1350 300 1290 482 1318 V1448 C330 1432 150 1472 0 1456Z" fill="#f87171"/>
      <path d="M0 1842 C150 1822 300 1852 482 1830 V2464 H0Z" fill="url(#homeFoot)"/>
      <path d="M0 2322 C150 2300 350 2334 482 2302 V2464 H0Z" fill="#fff"/>
    </svg>

    <header>
      <div class="logo-dot" style="left:41px;top:5px;width:24px;height:24px;font-size:4.5px">BRIGHT<br>NBR</div>
      <nav class="nav" style="font-size:6.5px">
        <a class="is-active" style="left:190px;top:12px">Home</a>
        <a style="left:225px;top:12px">About Us</a>
        <a style="left:271px;top:12px">Our Story</a>
        <a style="left:316px;top:12px">Social Impact</a>
      </nav>
      <div class="pill pill--dark" style="left:387px;top:7px;width:54px;height:19px;font-size:5.5px">Join Us</div>
    </header>

    <div class="a eyebrow" style="left:41px;top:88px;font-size:5.5px">Transparent Support</div>
    <div class="a heading" style="left:41px;top:101px;font-size:18px;font-weight:600">Social Inclusion</div>
    <div class="a" style="left:41px;top:124px;font-size:12px;color:var(--body);font-weight:300">If you can’t pay back</div>
    <div class="pill pill--coral" style="left:41px;top:148px;width:71px;height:18px;font-size:5.5px">Pay it forward</div>
    <div class="badge" style="left:41px;top:221px;width:59px;height:17px"></div>

    <!-- hero phones -->
    <div class="phone" style="left:241px;top:100px;width:78px;height:172px;font-size:5.6px">
      <div class="screen"><div class="notch"></div>
        <div class="ui-head"><span class="ui-dot"></span><span class="grow"></span><span class="ui-dot ui-dot--ring"></span><span class="ui-dot"></span></div>
        <div class="ui-search"></div>
        <div class="ui-grid"><i></i><i></i><i></i><i></i><i></i><i></i><i></i><i></i></div>
        <div class="ui-line"></div><div class="ui-line ui-line--soft"></div>
        <div class="ui-tiles"><i></i><i></i></div>
      </div>
    </div>
    <div class="phone" style="left:380px;top:100px;width:66px;height:170px;font-size:5px">
      <div class="screen"><div class="notch"></div>
        <div class="ui-head"><span class="grow"></span><span class="ui-dot"></span><span class="ui-dot"></span></div>
        <div class="ui-banner"></div>
        <div class="ui-grid"><i></i><i></i><i></i><i></i></div>
        <div class="ui-line"></div><div class="ui-line ui-line--soft"></div>
        <div class="ui-nav"><i></i><i></i><i></i><i></i></div>
      </div>
    </div>
    <div class="phone" style="left:298px;top:74px;width:84px;height:172px;font-size:5.6px">
      <div class="screen"><div class="notch"></div>
        <div class="ui-line"></div><div class="ui-line ui-line--soft"></div>
        <div class="ui-search" style="margin-top:.5em"></div>
        <div class="ui-tabs"><i></i><i></i></div>
        <div class="ui-row"><span class="ui-thumb"></span><span class="ui-text"><div class="ui-line"></div><div class="ui-line ui-line--soft ui-line--short"></div></span></div>
        <div class="ui-row"><span class="ui-thumb"></span><span class="ui-text"><div class="ui-line"></div><div class="ui-line ui-line--soft ui-line--short"></div></span></div>
        <div class="ui-row"><span class="ui-thumb"></span><span class="ui-text"><div class="ui-line"></div><div class="ui-line ui-line--soft ui-line--short"></div></span></div>
        <div class="ui-row"><span class="ui-thumb"></span><span class="ui-text"><div class="ui-line"></div><div class="ui-line ui-line--soft ui-line--short"></div></span></div>
      </div>
    </div>

    <div class="a eyebrow" style="left:0;width:482px;text-align:center;top:318px;font-size:6px">Target 2021</div>
    <div class="a heading" style="left:0;width:482px;text-align:center;top:331px;font-size:14px">Join the Bright Movement</div>

    <div class="card" style="left:40px;top:376px;width:120px;height:107px"></div>
    <div class="card" style="left:180px;top:376px;width:120px;height:107px"></div>
    <div class="card" style="left:320px;top:376px;width:120px;height:107px"></div>
    <div class="a heading" style="left:40px;width:120px;text-align:center;top:404px;font-size:13px">30,000</div>
    <div class="a heading" style="left:180px;width:120px;text-align:center;top:404px;font-size:13px">3,000</div>
    <div class="a heading" style="left:320px;width:120px;text-align:center;top:404px;font-size:13px">500</div>
    <div class="a" style="left:40px;width:120px;text-align:center;top:430px;font-size:5px;color:var(--body)">Contributors</div>
    <div class="a" style="left:180px;width:120px;text-align:center;top:430px;font-size:5px;color:var(--body)">Beneficiaries</div>
    <div class="a" style="left:320px;width:120px;text-align:center;top:430px;font-size:5px;color:var(--body)">Merchants</div>
    <div class="a link" style="left:40px;width:120px;text-align:center;top:445px;font-size:5px;text-decoration:underline">Pay it foward</div>
    <div class="a link" style="left:180px;width:120px;text-align:center;top:445px;font-size:5px;text-decoration:underline">Social Impact</div>
    <div class="a link" style="left:320px;width:120px;text-align:center;top:445px;font-size:5px;text-decoration:underline">Merchants</div>

    <div class="a eyebrow" style="left:0;width:482px;text-align:center;top:522px;font-size:5.5px">Our Partners</div>
    <div class="a" style="left:0;width:478px;text-align:center;top:532px;font-size:7.5px;color:var(--body);font-weight:300">A growing network and partnerships with the global organisations</div>
    <div class="partner" style="left:60px;top:564px;width:58px;height:14px;background:#d9d1ec"></div>
    <div class="partner" style="left:123px;top:565px;width:56px;height:12px;background:#d3d8e8"></div>
    <div class="partner" style="left:184px;top:561px;width:54px;height:20px;background:#d6dced"></div>
    <div class="partner" style="left:245px;top:560px;width:52px;height:22px;background:#f6dfcc"></div>
    <div class="partner" style="left:304px;top:558px;width:56px;height:24px;background:#d2dbef"></div>
    <div class="partner" style="left:366px;top:562px;width:54px;height:18px;background:#f7d4d4"></div>
    <div class="partner" style="left:60px;top:596px;width:56px;height:18px;background:#f4d6d8"></div>
    <div class="partner" style="left:138px;top:593px;width:54px;height:24px;background:#d3e2f3"></div>
    <div class="partner" style="left:212px;top:596px;width:56px;height:20px;background:#d3ecd8"></div>
    <div class="partner" style="left:278px;top:598px;width:80px;height:14px;background:#dcdcdc"></div>
    <div class="partner" style="left:366px;top:597px;width:56px;height:16px;background:#dcdde6"></div>

    <div class="photo" style="left:40px;top:688px;width:182px;height:136px;background:radial-gradient(ellipse 30% 55% at 35% 70%,#c0383e,transparent 70%),radial-gradient(ellipse 25% 30% at 38% 30%,#8a5a3e,transparent 70%),linear-gradient(90deg,#e8e4df,#f4efe9 60%,#d9cfc5)" role="img" aria-label="Video still of a woman in a red plaid shirt smiling at her phone"></div>
    <svg class="a" style="left:113px;top:740px" width="32" height="32" viewBox="0 0 32 32" aria-hidden="true"><circle cx="16" cy="16" r="16" fill="#161616"/><path d="M13 10 L22 16 L13 22Z" fill="#fff"/></svg>
    <div class="a eyebrow" style="left:262px;top:704px;font-size:5px">Lets talk about something good</div>
    <div class="a heading" style="left:262px;top:718px;font-size:14px">Hello, Bright Neighbours!</div>
    <p class="a copy" style="left:262px;top:742px;width:180px;font-size:5.5px">We digitalised the traditional concept of <span class="link">“Paying-it-for-ward”</span> to cultivate the new normal with timely help to include everyone. We strengthens the invisible community before it’s too late.</p>
    <div class="pill pill--coral" style="left:262px;top:790px;width:60px;height:18px;font-size:5px">Read more</div>

    <div class="photo" style="left:40px;top:899px;width:182px;height:163px;background:radial-gradient(ellipse 35% 40% at 62% 85%,#e0394d,transparent 70%),radial-gradient(ellipse 28% 35% at 62% 35%,#6a4430,transparent 70%),linear-gradient(180deg,#b9bcbd,#c8c6c1 50%,#8b8f90)" role="img" aria-label="Smiling curly-haired woman in a pink top at a laptop outdoors"></div>
    <div class="a eyebrow" style="left:262px;top:893px;font-size:5px">How it all began</div>
    <div class="a heading" style="left:262px;top:907px;font-size:14px">The Brand Story</div>
    <p class="a copy" style="left:262px;top:931px;width:180px;font-size:5.3px;line-height:1.6">Back in the <span class="link">1980s</span>, my family received generous donations and small handwritten notes containing good wishes through a newspaper fund raising for my mum’s medical expenses. I vividly remember some old and tattered notes from strangers. We ended up with double the amount that was needed, and my parents used the remaining sum to support other patients.</p>
    <div class="photo" style="left:262px;top:1009px;width:22px;height:22px;border-radius:50%;background:radial-gradient(circle at 50% 40%,#d9b29a,#7a5443)" role="img" aria-label="Founder portrait"></div>
    <svg class="a" style="left:296px;top:1010px" width="42" height="18" viewBox="0 0 42 18" role="img" aria-label="Founder signature"><path d="M3 13 C8 2 12 3 10 12 C14 6 20 8 24 11 C28 13 32 6 39 5" fill="none" stroke="#333" stroke-width=".8"/></svg>
    <div class="pill pill--coral" style="left:262px;top:1047px;width:60px;height:18px;font-size:5px">Read more</div>

    <div class="a eyebrow" style="left:40px;top:1151px;font-size:5px">No one left behind</div>
    <div class="a heading" style="left:40px;top:1165px;font-size:14px;white-space:normal;width:180px">Our Sustainable Development Goals</div>
    <p class="a copy" style="left:40px;top:1207px;width:190px;font-size:5.3px;line-height:1.7">Bright Neighbour is a social enterprise with 100% social impact outputs. <span class="link" style="text-decoration:underline">We serve as a transparent platform for businesses</span> to participate with a new approach of social responsibility towards the communities in need in a practical way.</p>
    <div class="pill pill--coral" style="left:40px;top:1258px;width:64px;height:18px;font-size:5px">Read more</div>
    <div class="photo" style="left:262px;top:1142px;width:179px;height:138px;background:linear-gradient(90deg,transparent 44%,rgba(90,70,50,.7) 44% 50%,transparent 50%),linear-gradient(180deg,#8f9ea3 0%,#60706c 30%,#28402f 50%,#1f3a2c 80%,#3b5f6b 100%)" role="img" aria-label="Forest valley with a suspended wooden ladder above a lake"></div>

    <div class="a" style="left:0;width:478px;text-align:center;top:1353px;font-size:7.5px;color:#fff">Unlock the greatness within you?</div>
    <div class="a" style="left:0;width:478px;text-align:center;top:1364px;font-size:13.5px;color:#fff">Want to do something good?</div>
    <div class="pill pill--white" style="left:207px;top:1390px;width:68px;height:18px;font-size:5px">Pay it foward</div>

    <div class="a eyebrow" style="left:0;width:478px;text-align:center;top:1485px;font-size:6.5px">Updates</div>
    <div class="a heading" style="left:0;width:478px;text-align:center;top:1494px;font-size:14px">Inspirations</div>

    <div class="card" style="left:40px;top:1535px;width:196px;height:238px;overflow:hidden">
      <div class="photo" style="left:0;top:0;width:196px;height:130px;border-radius:0;background:radial-gradient(ellipse 35% 55% at 58% 60%,#7a4a2c,transparent 70%),radial-gradient(ellipse 22% 25% at 55% 25%,#2a2422,transparent 70%),linear-gradient(180deg,#b4bfbf,#8f9d9a 60%,#5f6e6a)" role="img" aria-label="Person in a brown jacket with head bowed by the sea"></div>
    </div>
    <div class="a heading" style="left:59px;top:1677px;font-size:11.5px;white-space:normal;width:140px">Where does it come from?</div>
    <p class="a copy" style="left:59px;top:1712px;width:130px;font-size:5.5px">Neque porro quisquam est qui dolorem ipsum quia dolor sit amet,</p>
    <div class="pill pill--outline" style="left:58px;top:1738px;width:59px;height:17px;font-size:5px">Learn more</div>

    <div class="card" style="left:262px;top:1535px;width:179px;height:67px"></div>
    <div class="card" style="left:262px;top:1620px;width:179px;height:68px"></div>
    <div class="card" style="left:262px;top:1706px;width:179px;height:68px"></div>
    <div class="photo" style="left:262px;top:1535px;width:67px;height:67px;border-radius:8px 0 0 8px;background:radial-gradient(ellipse 30% 35% at 45% 55%,#c0383e,transparent 70%),linear-gradient(135deg,#e2d2bd,#c9a98a)" role="img" aria-label="Person in a red shirt crouching on a sandy shore"></div>
    <div class="photo" style="left:262px;top:1620px;width:67px;height:68px;border-radius:8px 0 0 8px;background:linear-gradient(180deg,#3a2c22,#c98a48 35%,#f0c070 50%,#2a2019 62%)" role="img" aria-label="Silhouette resting on rocks at sunset"></div>
    <div class="photo" style="left:262px;top:1706px;width:67px;height:68px;border-radius:8px 0 0 8px;background:radial-gradient(circle at 40% 40%,#7aa04a,transparent 45%),linear-gradient(135deg,#3e4a2e,#6a4c36)" role="img" aria-label="Volunteer hands holding seedlings"></div>
    <div class="a heading" style="left:340px;top:1541px;font-size:6px">Where does it come from?</div>
    <p class="a copy" style="left:340px;top:1551px;width:90px;font-size:5.3px;line-height:1.5">Neque porro quisquam est qui dolorem ipsum quia dolor sit amet,</p>
    <div class="a link" style="left:340px;top:1586px;font-size:3.8px">LEARN MORE</div>
    <div class="a heading" style="left:340px;top:1627px;font-size:6px">Where does it come from?</div>
    <p class="a copy" style="left:340px;top:1637px;width:90px;font-size:5.3px;line-height:1.5">Neque porro quisquam est qui dolorem ipsum quia dolor sit amet,</p>
    <div class="a link" style="left:340px;top:1672px;font-size:3.8px">LEARN MORE</div>
    <div class="a heading" style="left:340px;top:1713px;font-size:6px">Where does it come from?</div>
    <p class="a copy" style="left:340px;top:1723px;width:90px;font-size:5.3px;line-height:1.5">Neque porro quisquam est qui dolorem ipsum quia dolor sit amet,</p>
    <div class="a link" style="left:340px;top:1758px;font-size:3.8px">LEARN MORE</div>

    <div class="a heading" style="left:0;width:496px;text-align:center;top:1862px;font-size:13.5px">Social media feeds</div>
    <div class="photo" style="left:40px;top:1903px;width:121px;height:102px;background:radial-gradient(ellipse 30% 40% at 50% 95%,#e88a8a,transparent 70%),radial-gradient(ellipse 22% 40% at 50% 40%,#5a3a2a,transparent 70%),linear-gradient(180deg,#2f9fc9,#45b4d6)" role="img" aria-label="Smiling woman against a blue wall"></div>
    <div class="photo" style="left:180px;top:1903px;width:121px;height:102px;background:radial-gradient(ellipse 35% 45% at 65% 75%,#f2f0ee,transparent 70%),linear-gradient(90deg,#8a6a50,#c9b6a2 40%,#e9e5e0)" role="img" aria-label="Woman on a phone call in a bright room"></div>
    <div class="photo" style="left:320px;top:1903px;width:121px;height:102px;background:linear-gradient(180deg,#5f7fb0 0%,#9aa7c4 30%,#d99a58 55%,#3a3a4e 70%,#1e2a44 100%)" role="img" aria-label="City skyline across the bay at dusk"></div>
    <div class="photo" style="left:40px;top:2025px;width:121px;height:102px;background:radial-gradient(ellipse 40% 50% at 55% 55%,#1e1e22,transparent 70%),linear-gradient(135deg,#5a4030,#a07a5a)" role="img" aria-label="Two colleagues looking at a phone together"></div>
    <div class="photo" style="left:180px;top:2025px;width:121px;height:102px;background:radial-gradient(ellipse 35% 45% at 55% 65%,#f0c030,transparent 70%),linear-gradient(180deg,#e8dcc0,#d8c9a8 60%,#c7a46a)" role="img" aria-label="Woman in a yellow sweater using a phone"></div>
    <div class="photo" style="left:320px;top:2025px;width:121px;height:102px;background:radial-gradient(ellipse 25% 45% at 65% 65%,#3a3e4e,transparent 70%),radial-gradient(ellipse 25% 35% at 25% 80%,#a8624a,transparent 70%),linear-gradient(180deg,#9fb2c4,#c7ccd2)" role="img" aria-label="Senior colleagues reviewing a tablet"></div>

    <div class="a" style="left:40px;top:2172px;font-size:14px;color:var(--coral);font-weight:500">Subscribe</div>
    <div class="a heading" style="left:40px;top:2190px;font-size:13px">to Our Newsletter</div>
    <p class="a copy" style="left:40px;top:2218px;width:130px;font-size:5px">Let’s stay in touch! We would like to keep you inspired with our Kindness stories and community events.</p>
    <div class="field" style="left:203px;top:2176px;width:107px;height:23px;padding-left:10px;font-size:5.5px">Email</div>
    <div class="field" style="left:333px;top:2176px;width:108px;height:23px;padding-left:12px;font-size:5.5px">Name</div>
    <div class="check" style="left:203px;top:2217px;width:9px;height:9px"></div>
    <div class="a" style="left:224px;top:2218px;font-size:5.5px">By continuing, you accept the privacy policy</div>
    <div class="pill pill--dark" style="left:203px;top:2246px;width:66px;height:20px;font-size:5.5px">Subscribe</div>

    <div class="logo-dot" style="left:40px;top:2343px;width:32px;height:32px;font-size:5.5px">BRIGHT<br>NBR</div>
    <div class="a" style="left:95px;top:2342px;font-size:5.5px;font-weight:500">Follow us and stay updated!</div>
    <div class="a" style="left:95px;top:2361px;font-size:5px;color:var(--body)">A Singapore Social Enterprise.</div>
    <div class="a" style="left:95px;top:2370px;font-size:5px;color:var(--body)">In a world where you can be anything, be kind.</div>
    <div class="social" style="left:95px;top:2387px;width:12px;height:12px"></div>
    <div class="social" style="left:113px;top:2387px;width:12px;height:12px"></div>
    <div class="social" style="left:131px;top:2387px;width:12px;height:12px"></div>
    <div class="a" style="left:297px;top:2342px;font-size:5.5px;font-weight:500">Get To Know Us</div>
    <ul class="bullets" style="left:297px;top:2360px;font-size:5px;line-height:1.8">
      <li>Home</li><li>About Us</li><li>Our Story</li><li>Social Impact</li><li>Bright Neighbour</li>
    </ul>
    <ul class="bullets" style="left:368px;top:2361px;font-size:5px;line-height:1.7">
      <li>Bright Business</li><li>Merchant</li><li>The Bright Gift</li><li>FAQs</li><li>Contact Us</li>
    </ul>
    <div class="copyright" style="top:2437px;font-size:5.5px">Copyright © 2021 Bright Neighbour Singapore</div>
  </section>

  <section class="page page--about">
    <svg class="backdrop" width="642" height="2464" viewBox="0 0 642 2464" aria-hidden="true">
      <defs>
        <linearGradient id="aboutMid" x1="0" y1="0" x2="0" y2="1">
          <stop offset="0" stop-color="#ffffff"/>
          <stop offset="1" stop-color="#ffc9cc"/>
        </linearGradient>
        <linearGradient id="aboutFoot" x1="0" y1="0" x2="0" y2="1">
          <stop offset="0" stop-color="#ffffff"/>
          <stop offset="1" stop-color="#ffcfd2"/>
        </linearGradient>
      </defs>
      <path d="M220 0 H642 V140 C600 162 520 122 460 112 C360 94 296 82 220 0Z" fill="#ffd3d5"/>
      <path d="M0 580 C200 560 450 600 642 560 V1520 C500 1562 300 1470 0 1546Z" fill="url(#aboutMid)"/>
      <path d="M0 1992 C200 1970 450 2010 642 1980 V2464 H0Z" fill="url(#aboutFoot)"/>
      <path d="M0 2240 C200 2218 450 2252 642 2208 V2464 H0Z" fill="#fff"/>
    </svg>

    <header>
      <div class="logo-dot" style="left:54px;top:6px;width:32px;height:32px;font-size:6px">BRIGHT<br>NBR</div>
      <nav class="nav" style="font-size:10px">
        <a class="is-active" style="left:252px;top:15px">Home</a>
        <a style="left:300px;top:15px">About Us</a>
        <a style="left:360px;top:15px">Our Story</a>
        <a style="left:421px;top:15px">Social Impact</a>
      </nav>
      <div class="pill pill--dark" style="left:516px;top:9px;width:72px;height:25px;font-size:7.5px">Join Us</div>
    </header>

    <div class="a eyebrow" style="left:53px;top:146px;font-size:7.5px">Who we are</div>
    <div class="a heading" style="left:53px;top:158px;font-size:28px">About Us</div>
    <div class="a" style="left:53px;top:195px;font-size:16.5px;color:var(--body);font-weight:300;line-height:1.4">If you can’t pay<br>back Pay it forward</div>
    <div class="photo" style="left:296px;top:113px;width:292px;height:213px;border-radius:12px;background:radial-gradient(ellipse 22% 40% at 30% 65%,#f2b8c8,transparent 70%),radial-gradient(ellipse 20% 35% at 52% 60%,#cfd8e8,transparent 70%),radial-gradient(ellipse 18% 40% at 70% 40%,#8a96a8,transparent 70%),linear-gradient(180deg,#5a4a3e 0%,#8a7a6a 35%,#e9e6e2 80%,#d2ccc4)" role="img" aria-label="Team of colleagues gathered around a laptop in an office"></div>
    <div class="badge" style="left:508px;top:340px;width:80px;height:22px"></div>

    <div class="card" style="left:55px;top:394px;width:160px;height:143px"></div>
    <div class="card" style="left:242px;top:394px;width:160px;height:143px"></div>
    <div class="card" style="left:428px;top:394px;width:160px;height:143px"></div>
    <div class="a heading" style="left:73px;top:413px;font-size:13.5px">Our Philosophy</div>
    <div class="a heading" style="left:262px;top:413px;font-size:13.5px">Our Mission</div>
    <div class="a heading" style="left:447px;top:413px;font-size:13.5px">Our Future</div>
    <p class="a copy" style="left:73px;top:440px;width:128px;font-size:7.5px">We believe in authentic social responsibility is driven from individuals and businesses.</p>
    <p class="a copy" style="left:262px;top:440px;width:126px;font-size:7.5px">We connect individuals and businesses to support where it needs most in an easy, transparent, and holistic way through our platform.</p>
    <p class="a copy" style="left:447px;top:440px;width:126px;font-size:7.5px">Together, social impact as part of DNA at the heart of every consumption and business.</p>

    <svg class="a" style="left:55px;top:607px" width="240" height="240" viewBox="0 0 240 240" aria-hidden="true"><circle cx="120" cy="120" r="120" fill="#fbbcbf"/></svg>
    <div class="phone phone--crop" style="left:110px;top:658px;width:130px;height:190px;font-size:9.5px">
      <div class="screen"><div class="notch"></div>
        <div class="ui-head"><span class="ui-dot"></span><span class="grow"></span><span class="ui-dot"></span><span class="ui-dot ui-dot--ring"></span></div>
        <div class="ui-search"></div>
        <div class="ui-grid"><i></i><i></i><i></i><i></i><i></i><i></i><i></i><i></i></div>
        <div class="ui-line"></div><div class="ui-line ui-line--soft"></div>
        <div class="ui-tiles"><i></i><i></i></div>
      </div>
    </div>
    <div class="a eyebrow" style="left:350px;top:634px;font-size:8px;letter-spacing:0">Geting involved</div>
    <div class="a heading" style="left:350px;top:653px;font-size:20px">Contributors</div>
    <p class="a copy" style="left:350px;top:684px;width:230px;font-size:8px">You can Pay-it-forward products and services listings on our platform just like any other e-commerce platform with Kind Messages.</p>
    <p class="a copy" style="left:350px;top:735px;width:230px;font-size:8px">The platform will match with beneficiary who require the contributions with the personalized kind message.</p>
    <p class="a copy" style="left:350px;top:773px;width:230px;font-size:8px">Contributor will receive an alert once the beneficiary claims their contributions.</p>

    <div class="a eyebrow" style="left:55px;top:935px;font-size:8px;letter-spacing:0">Geting involved</div>
    <div class="a heading" style="left:55px;top:954px;font-size:20px">Merchants</div>
    <p class="a copy" style="left:55px;top:985px;width:240px;font-size:8px">Our free listing platform allow merchants to upload and list the available goods and services.</p>
    <p class="a copy" style="left:55px;top:1023px;width:240px;font-size:8px">Beneficiary or their representative make the booking and contact the merchant to claim the contributions directly with redemption code verifications.</p>
    <svg class="a" style="left:347px;top:892px" width="240" height="240" viewBox="0 0 240 240" aria-hidden="true"><circle cx="120" cy="120" r="120" fill="#fbe6a6"/></svg>
    <div class="phone phone--crop" style="left:406px;top:942px;width:130px;height:190px;font-size:9.5px">
      <div class="screen"><div class="notch"></div>
        <div class="ui-head"><span class="grow"><div class="ui-line" style="width:70%;margin:0"></div></span><span class="ui-dot"></span></div>
        <div class="ui-line ui-line--soft"></div>
        <div class="ui-search" style="margin-top:.4em;margin-bottom:.2em"></div>
        <div class="ui-tabs"><i></i><i></i></div>
        <div class="ui-row"><span class="ui-thumb"></span><span class="ui-text"><div class="ui-line"></div><div class="ui-line ui-line--soft ui-line--short"></div></span></div>
        <div class="ui-row"><span class="ui-thumb"></span><span class="ui-text"><div class="ui-line"></div><div class="ui-line ui-line--soft ui-line--short"></div></span></div>
        <div class="ui-row"><span class="ui-thumb"></span><span class="ui-text"><div class="ui-line"></div><div class="ui-line ui-line--soft ui-line--short"></div></span></div>
      </div>
    </div>

    <svg class="a" style="left:36px;top:1188px" width="240" height="240" viewBox="0 0 240 240" aria-hidden="true"><circle cx="120" cy="120" r="120" fill="#fdd6bd"/></svg>
    <div class="phone phone--crop" style="left:88px;top:1234px;width:134px;height:180px;font-size:9.5px">
      <div class="screen"><div class="notch"></div>
        <div class="ui-head"><span class="ui-dot"></span><span class="grow"></span><span class="ui-dot ui-dot--ring"></span></div>
        <div class="ui-search"></div>
        <div class="ui-banner"></div>
        <div class="ui-line"></div>
        <div class="ui-grid" style="margin-top:.5em"><i></i><i></i><i></i><i></i></div>
      </div>
    </div>
    <div class="a eyebrow" style="left:331px;top:1216px;font-size:8px;letter-spacing:0">Geting involved</div>
    <div class="a heading" style="left:331px;top:1235px;font-size:20px">Contributors</div>
    <p class="a copy" style="left:331px;top:1266px;width:240px;font-size:8px">You can Pay-it-forward products and services listings on our platform just like any other e-commerce platform with Kind Messages.</p>
    <p class="a copy" style="left:331px;top:1317px;width:240px;font-size:8px">The platform will match with beneficiary who require the contributions with the personalized kind message.</p>
    <p class="a copy" style="left:331px;top:1355px;width:240px;font-size:8px">Contributor will receive an alert once the beneficiary claims their contributions.</p>

    <div class="a eyebrow" style="left:55px;top:1600px;font-size:7.5px;letter-spacing:0">Whats on your mind</div>
    <div class="a heading" style="left:53px;top:1615px;font-size:20px">Frequently Asked Question</div>
    <p class="a copy" style="left:53px;top:1640px;width:285px;font-size:8px">Everyday has its share of challenging moments Anyone can experience tough times in their life. That’s why we need timely Help</p>
    <div class="faq-item" style="top:1680px">What’s so unique about the double impact?</div>
    <div class="faq-item" style="top:1711px">How is this different from other government or NGO initiatives?</div>
    <div class="faq-item" style="top:1742px">Are you able to issue tax-deductible receipts?</div>
    <div class="faq-item" style="top:1773px">What is the legitimacy behind the concept of your organisation?</div>
    <div class="faq-item" style="top:1803px">Do you accept lump-sum cash contributions?</div>
    <div class="faq-item" style="top:1834px">Will contributors receive updates on how their contributions are being used?</div>
    <div class="faq-item" style="top:1865px">Will the beneficiaries know the personal details of the individual contributor?</div>
    <div class="faq-item" style="top:1896px">Can a contributor choose to remain undisclosed?</div>
    <div class="photo" style="left:349px;top:1672px;width:239px;height:226px;border-radius:12px;background:radial-gradient(ellipse 30% 45% at 55% 50%,#6a4230,transparent 70%),radial-gradient(ellipse 30% 30% at 75% 95%,#3a3a5a,transparent 70%),linear-gradient(180deg,#7fb8e4,#b9dcf4)" role="img" aria-label="Smiling woman talking on a phone against a blue sky"></div>

    <div class="a" style="left:53px;top:2045px;font-size:20px;color:var(--coral);font-weight:500">Subscribe</div>
    <div class="a heading" style="left:53px;top:2070px;font-size:20px">to Our Newsletter</div>
    <p class="a copy" style="left:53px;top:2108px;width:175px;font-size:7.5px">Let’s stay in touch! We would like to keep you inspired with our Kindness stories and community events.</p>
    <div class="field" style="left:270px;top:2052px;width:144px;height:32px;padding-left:14px;font-size:8px">Email</div>
    <div class="field" style="left:443px;top:2052px;width:145px;height:32px;padding-left:14px;font-size:8px">Name</div>
    <div class="check" style="left:270px;top:2106px;width:14px;height:14px"></div>
    <div class="a" style="left:298px;top:2107px;font-size:9px;font-weight:500">By continuing, you accept the privacy policy</div>
    <div class="pill pill--dark" style="left:270px;top:2145px;width:88px;height:28px;font-size:8px">Subscribe</div>

    <div class="logo-dot" style="left:54px;top:2274px;width:44px;height:44px;font-size:7px">BRIGHT<br>NBR</div>
    <div class="a" style="left:128px;top:2273px;font-size:8px;font-weight:500">Follow us and stay updated!</div>
    <div class="a" style="left:126px;top:2298px;font-size:7.5px;color:var(--body)">A Singapore Social Enterprise.</div>
    <div class="a" style="left:126px;top:2311px;font-size:7.5px;color:var(--body)">In a world where you can be anything, be kind.</div>
    <div class="social" style="left:128px;top:2334px;width:16px;height:16px"></div>
    <div class="social" style="left:151px;top:2334px;width:16px;height:16px"></div>
    <div class="social" style="left:174px;top:2334px;width:16px;height:16px"></div>
    <div class="a" style="left:395px;top:2273px;font-size:8px;font-weight:500">Get To Know Us</div>
    <ul class="bullets" style="left:395px;top:2297px;font-size:7.5px;line-height:1.7">
      <li>Home</li><li>About Us</li><li>Our Story</li><li>Social Impact</li><li>Bright Neighbour</li>
    </ul>
    <ul class="bullets" style="left:494px;top:2299px;font-size:7.5px;line-height:1.7">
      <li>Bright Business</li><li>Merchant</li><li>The Bright Gift</li><li>FAQs</li><li>Contact Us</li>
    </ul>
    <div class="copyright" style="top:2400px;font-size:8px">Copyright © 2021 Bright Neighbour Singapore</div>
  </section>

</div>
</body>
</html>
```